Help us stand out from the crowd - Court of Maywell

We are a luxury watch business and are looking to develop our own paperwork that we can issue with our watches etc. I am looking for the following documents to be designed: Invoice, Warranty card, Insurance valuation, instruction booklet and a small folder to keep it all in. Need it to be small though. I have attached some images of my friends ones that look fantastic.

Target Market(s)

High net worth watch enthusiasts

Requirements
Must have
• Must be clean, precise and very easy on the eye. Think Vornel but underpinned with a classic british feel.
Should not have
• Shouldn't be dark.

```html
<!DOCTYPE html>
<html lang="en">
<head>
<meta charset="utf-8">
<title>Court of Maywell – Warranty Card</title>
<link rel="stylesheet" href="https://fonts.googleapis.com/css2?family=Outfit:wght@300;400;500&display=swap">
<style>
  :root {
    --backdrop: #5e5e5e;
    --card: #ffffff;
    --ink: #111111;
    --ink-soft: #2a2a2a;
    --rule: #555555;
    --ring: #efefef;
    --notice: #ffffff;
  }
  * { box-sizing: border-box; margin: 0; padding: 0; }
  html, body { width: 1200px; height: 1200px; overflow: hidden; }
  body { background: var(--backdrop); position: relative; font-family: "Outfit", sans-serif; }

  .card {
    position: absolute;
    left: 263px;
    width: 672px;
    height: 441px;
    background: var(--card);
    border-radius: 31px;
    overflow: hidden;
  }
  .card--front { top: 67px; }
  .card--back { top: 584px; }

  .card__rings { position: absolute; inset: 0; }

  .brand {
    position: absolute;
    left: 0; right: 0;
    top: 236px;
    text-align: center;
    font-weight: 400;
    font-size: 38px;
    letter-spacing: 7px;
    padding-left: 7px;
    color: var(--ink);
    line-height: 1;
  }
  .brand__motto {
    position: absolute;
    left: 0; right: 0;
    top: 306px;
    text-align: center;
    font-weight: 400;
    font-size: 17px;
    letter-spacing: 4.5px;
    padding-left: 4.5px;
    color: var(--ink);
    line-height: 1;
  }

  .warranty__title {
    position: absolute;
    left: 0; right: 0;
    top: 25px;
    text-align: center;
    font-weight: 300;
    font-size: 42px;
    color: var(--ink);
    line-height: 1;
  }
  .warranty__fields {
    position: absolute;
    left: 38px;
    top: 125px;
    width: 580px;
    list-style: none;
    border-top: 1.5px solid var(--rule);
  }
  .warranty__field {
    height: 38.5px;
    border-bottom: 1.5px solid var(--rule);
    font-weight: 300;
    font-size: 22px;
    color: var(--ink-soft);
    padding-left: 2px;
    line-height: 37px;
  }
  .warranty__contact {
    position: absolute;
    left: 0; right: 0;
    top: 361px;
    text-align: center;
    font-weight: 300;
    font-size: 20.5px;
    color: var(--ink);
    line-height: 25px;
  }
  .warranty__contact .sep { margin: 0 14px; }

  .notice {
    position: absolute;
    left: 0; right: 0;
    top: 1078px;
    text-align: center;
    font-weight: 500;
    font-size: 54px;
    color: var(--notice);
    line-height: 1;
  }
</style>
</head>
<body>
  <section class="card card--front">
    <svg class="card__rings" width="672" height="441" viewBox="0 0 672 441" aria-hidden="true">
      <circle cx="672" cy="-75" r="222" fill="none" stroke="var(--ring)" stroke-width="34"/>
      <circle cx="-19" cy="559" r="262" fill="none" stroke="var(--ring)" stroke-width="33"/>
    </svg>
    <h1 class="brand">COURT OF MAYWELL</h1>
    <p class="brand__motto">PRECISION KEPT, WORN WITH CARE</p>
  </section>

  <section class="card card--back">
    <h2 class="warranty__title">ONE YEAR WARRANTY</h2>
    <ul class="warranty__fields">
      <li class="warranty__field">Name</li>
      <li class="warranty__field">Model</li>
      <li class="warranty__field">Seriel Number</li>
      <li class="warranty__field">Dial</li>
      <li class="warranty__field">Date of purchase</li>
    </ul>
    <p class="warranty__contact">
      www.courtofmaywell.com<span class="sep">|</span>(+31) 612048395<br>
      Lindenkade 27, 3012 KN Rotterdam, Netherlands
    </p>
  </section>

  <p class="notice">PLEASE CHECK YOU MESSAGES.</p>
</body>
</html>
```